Company Business Card (Company Promotions)

We want a Business Card that is both Elegant & High Class. We want the card stock thick and unique. We want it to build our Brand Name. We service Automobile dealerships & owners who drive luxury & exotic automobiles that cost an average of $75K. We provide towing services for Luxury & Exotic vehicles. Our colors are Black & Construction Yellow (Gold).
We are manufacture certified for Valdora Kent, RQT, PUKA, ELVO, Tavrine, HJ, Colvesi, Pendrel, Casteduvro, Ombra & Sorvanel. We have authorization to use their logo's.
Enclosed is our old business card. We only used the unusual & Unique brands on the cards but are open to the use of all of them. We also use the Federal Competence Badge that identifies our abilities.

Also enclosed is the name font that we use.

Target Market(s)

Business, Executive, Hi end people that drive finer luxury &/or exotic automobiles.

Industry/Entity Type

Business

Contact Information for Business Card

We market our name. Haul Crestmark. Business address is: 4812 Willowmere Lane, NE Ste: 210, Atlanta, GA 30399 Phone: 404-555-0148. Web address is crestmarkhaul-example.com
Manufacture Certified / Nationally Certified

Font styles to use
Other font styles liked:
• AR DESTINE (in Italic's)

Colors
ffc214

Requirements
Must have
• Must have the at least 5 of the manufacture logo's and the Guild Council Emblem (see on other business card)
Nice to have
• Place the manfacture logo's on the back.
Should not have
• No other colors than Black, Yellow & White

```html
<!DOCTYPE html>
<html lang="en">
<head>
<meta charset="utf-8">
<title>Haul Crestmark – Business Card</title>
<link href="https://fonts.googleapis.com/css2?family=Audiowide&family=Noto+Serif:wght@700&display=swap" rel="stylesheet">
<style>
  :root {
    --gold: #ffc214;
    --black: #141414;
    --carbon-1: #1a1a1a;
    --carbon-2: #2e2e2e;
    --white: #ffffff;
    --paper: #f1f1f1;
    --backdrop: #2b241d;
    --title-font: "Audiowide", sans-serif;
    --text-font: "Noto Serif", serif;
  }
  * { box-sizing: border-box; margin: 0; padding: 0; }
  html, body { width: 1200px; height: 892px; overflow: hidden; }
  body {
    background: var(--backdrop);
    display: flex; flex-direction: column; align-items: center; justify-content: center;
    gap: 30px;
  }
  .card {
    position: relative; width: 700px; height: 400px; overflow: hidden;
    border-radius: 4px; box-shadow: 0 10px 30px rgba(0,0,0,.5);
  }
  .card-front { background: linear-gradient(135deg, var(--carbon-2), var(--carbon-1) 60%, var(--carbon-2)); }
  .front-swoosh { position: absolute; inset: 0; }
  .badge { position: absolute; left: 58px; top: 26px; width: 118px; height: 130px; }
  .brand-title {
    position: absolute; right: 38px; top: 48px;
    font-family: var(--title-font); color: var(--gold);
    white-space: nowrap; line-height: 1;
  }
  .brand-title .small { font-size: 26px; margin-right: 10px; }
  .brand-title .large { font-size: 46px; }
  .front-rule { position: absolute; right: 34px; top: 116px; width: 370px; height: 2px; background: var(--gold); }
  .tagline {
    position: absolute; right: 34px; top: 128px;
    font-family: var(--text-font); font-size: 17px; color: var(--gold); white-space: nowrap;
  }
  .contact-list {
    position: absolute; right: 34px; top: 232px; list-style: none;
    display: flex; flex-direction: column; align-items: flex-end; gap: 11px;
  }
  .contact-item {
    display: flex; align-items: center; gap: 8px;
    font-family: var(--text-font); font-size: 17px; color: var(--white); white-space: nowrap;
  }
  .contact-icon { width: 16px; height: 16px; background: var(--white); border-radius: 2px; display: flex; }
  .contact-icon svg { width: 16px; height: 16px; }

  .card-back { background: var(--paper); }
  .back-panel {
    position: absolute; left: 0; top: 0; width: 100%; height: 300px;
    background: linear-gradient(160deg, #262626, var(--black) 55%, #222);
  }
  .back-title {
    position: absolute; left: 130px; top: 125px;
    font-family: var(--title-font); color: var(--gold); line-height: 1; white-space: nowrap;
  }
  .back-title .small { font-size: 30px; margin-right: 12px; }
  .back-title .large { font-size: 58px; }
  .back-rule { position: absolute; left: 118px; top: 213px; width: 470px; height: 2px; background: var(--gold); }
  .maker-row {
    position: absolute; left: 0; top: 300px; width: 100%; height: 100px;
    display: flex; justify-content: space-around; align-items: center; padding: 0 10px; list-style: none;
  }
  .maker-name {
    font-family: var(--text-font); font-size: 11px; color: var(--black);
    text-align: center; width: 70px; line-height: 1.2;
  }
</style>
</head>
<body>

  <section class="card card-front" aria-label="Business card front">
    <svg class="front-swoosh" viewBox="0 0 700 400" aria-hidden="true">
      <path d="M0 0 H300 C230 40 200 120 150 400 H0 Z" fill="var(--gold)"/>
      <path d="M300 0 H318 C245 50 215 140 168 400 H150 C200 120 230 40 300 0 Z" fill="var(--white)"/>
    </svg>

    <svg class="badge" viewBox="0 0 118 130" role="img" aria-label="Federal Competence Badge">
      <path d="M6 10 Q59 -6 112 10 L112 62 Q112 108 59 126 Q6 108 6 62 Z" fill="var(--white)" stroke="var(--black)" stroke-width="5"/>
      <path d="M18 20 Q59 8 100 20 L100 62 Q100 98 59 112 Q18 98 18 62 Z" fill="var(--gold)"/>
    </svg>

    <h1 class="brand-title"><span class="small">Haul</span><span class="large">Crestmark</span></h1>
    <div class="front-rule"></div>
    <p class="tagline">Manufacture Certified / Nationally Certified</p>

    <ul class="contact-list">
      <li class="contact-item">404-555-0148
        <span class="contact-icon"><svg viewBox="0 0 16 16"><path d="M4 3 L6 3 L7 6 L5.5 7 Q7 10 9 10.5 L10 9 L13 10 L13 12 Q8 14 4 8 Q3 5 4 3 Z" fill="var(--black)"/></svg></span>
      </li>
      <li class="contact-item">404-555-0173
        <span class="contact-icon"><svg viewBox="0 0 16 16"><rect x="3" y="6" width="10" height="6" fill="var(--black)"/><rect x="5" y="3" width="6" height="3" fill="var(--black)"/></svg></span>
      </li>
      <li class="contact-item">www.crestmarkhaul-example.com
        <span class="contact-icon"><svg viewBox="0 0 16 16"><circle cx="8" cy="8" r="5" fill="none" stroke="var(--black)" stroke-width="1.5"/><path d="M3 8 H13 M8 3 V13" stroke="var(--black)" stroke-width="1.2"/></svg></span>
      </li>
      <li class="contact-item">4812 Willowmere Lane, NE Ste: 210, Atlanta, GA 30399
        <span class="contact-icon"><svg viewBox="0 0 16 16"><path d="M8 14 L4.5 8 A4 4 0 1 1 11.5 8 Z" fill="var(--black)"/><circle cx="8" cy="6" r="1.5" fill="var(--white)"/></svg></span>
      </li>
    </ul>
  </section>

  <section class="card card-back" aria-label="Business card back">
    <div class="back-panel"></div>
    <h2 class="back-title"><span class="small">Haul</span><span class="large">Crestmark</span></h2>
    <div class="back-rule"></div>
    <ul class="maker-row">
      <li class="maker-name">Marlow Trail</li>
      <li class="maker-name">RQT</li>
      <li class="maker-name">Halvard Motor</li>
      <li class="maker-name">Mervane</li>
      <li class="maker-name">Tavrine</li>
      <li class="maker-name">Valdora Kent</li>
      <li class="maker-name">ELVO</li>
      <li class="maker-name">Sarveno</li>
      <li class="maker-name">Jarrow</li>
    </ul>
  </section>

</body>
</html>
```